Indie author needs a minimalist book cover

I need a book cover for my latest book on personal finance and investing. The book is called, "The Quiet Ledger: Habits for Lasting Security, Calm Savings, and a Full Future". This is volume one of a three part series on the FI/RE movement, which stands for 'Financial Independence/Retire Early'. This book is on the foundational principles of FI/RE and details the specific steps that these 'Quiet Ledger' involved in this community have done to position themselves to retire from paid work and live the life of their dreams - many only in their 20's, 30's and early 40's.

Title: The Quiet Ledger
Author: KB Morrow
Volume 1: Foundations
Book dimensions: 6"x9"

Book Blurb (for back cover):

Let's face it, no one wants to be different. But sometimes following the 'normal' crowd gets you no further than that crowd.

When it comes to money, the normal crowd is your typical consumer. Deep in debt, struggling to make ends meet, but still spending money on the newest 'thing' that just came out.

But there's another group that's been forming - right on the fringes of the personal finance world. I call them The Quiet Ledger. This book is about these superheroes of personal finance.

In it, you will learn:
• Who The Quiet Ledger are and what is this FI/RE Movement they are apart of
• What basic strategy they use to control their money
• How they became debt-free - and how you can join them
• How to use the PL/AN Keystone to help you really move the needle towards financial independence
• How to diversify your income with a side-hustle and which one to choose
• The money outlier savings plan that will allow you to reach financial independence in ten years or less

This first book in The Quiet Ledger series is about building a solid foundation so you and your family can become Quiet Ledger, reach financial freedom, retire early, and live a rich life.

Target Market(s)

Individuals looking to take control of their money, reach financial independence, and retire early.

Font styles to use
Sans Serif
Other font styles liked:
• Arvo

Colors

Designer to choose colors to be used in the design.

Requirements
Must have
• A minimalist design (see examples), the title of the book, my author name, and the volume number and name (see below).
• My vision for the cover is to have a way to represent an 'outlier' in a simple, minimalistic way. I'm not set on any specific design - I'm open to what the designers come up with; I don't want to hold back anyone's creativity.
• Title: The Quiet Ledger
• Author: KB Morrow
• Volume 1: Foundations
• Book Blurb (for back cover):
• Let's face it, no one wants to be different. But sometimes following the 'normal' crowd gets you no further than that crowd.
• When it comes to money, the normal crowd is your typical consumer. Deep in debt, struggling to make ends meet, but still spending money on the newest 'thing' that just came out.
• But there's another group that's been forming - right on the fringes of the personal finance world. I call them The Quiet Ledger. This book is about these superheroes of personal finance.
• In it, you will learn:
• • Who The Quiet Ledger are and what is this FI/RE Movement they are apart of
• • What basic strategy they use to control their money
• • How they became debt-free - and how you can join them
• • How to use the PL/AN Keystone to help you really move the needle towards financial independence
• • How to diversify your income with a side-hustle and which one to choose
• • The money outlier savings plan that will allow you to reach financial independence in ten years or less
• This first book in The Quiet Ledger series is about building a solid foundation so you and your family can become Quiet Ledger, reach financial freedom, retire early, and live a rich life.
Nice to have
• The subtitle - but only if it's not too crowded. Like I said before, I'm more interested in maintaining a minimalist aesthetic.
• The subtitle is: "Habits for Lasting Security, Calm Savings, And A Full Future"
Should not have
• Too many colors or objects on the cover.

```html
<!DOCTYPE html>
<html lang="en">
<head>
<meta charset="utf-8">
<title>The Quiet Ledger — KB Morrow</title>
<link rel="stylesheet" href="https://fonts.googleapis.com/css2?family=Arvo:wght@400;700&family=EB+Garamond:wght@400&family=Cormorant+Garamond:wght@500&display=swap">
<style>
  :root {
    --stage: #e8e4df;
    --cover: #ffffff;
    --ink-grey: #5a5a5a;
    --brown-light: #8b5e3c;
    --brown-dark: #5b3412;
    --rule: #b08c66;
    --art-red: #c81e22;
    --art-grey: #8a8a8a;
  }
  * { margin: 0; padding: 0; box-sizing: border-box; }
  html, body { width: 1200px; height: 1200px; overflow: hidden; background: var(--stage); }
  .cover {
    position: absolute; left: 240px; top: 60px;
    width: 720px; height: 1080px;
    background: linear-gradient(180deg, var(--cover) 0%, #f6f6f5 100%);
    box-shadow: 0 10px 30px rgba(0,0,0,.12);
  }
  .author {
    position: absolute; top: 112px; left: 0; right: 0;
    text-align: center;
    font-family: "Cormorant Garamond", serif;
    font-weight: 500; font-size: 50px; letter-spacing: 0.32em;
    color: var(--ink-grey); padding-left: 0.32em;
  }
  .outlier-art {
    position: absolute; top: 235px; left: 150px;
    width: 420px; height: 260px;
    border-radius: 12px;
    background: radial-gradient(ellipse 22% 55% at 50% 50%, var(--art-red) 0%, rgba(200,30,34,.6) 45%, rgba(138,138,138,.85) 70%, rgba(138,138,138,.25) 100%);
  }
  .title-block {
    position: absolute; top: 555px; left: 108px; width: 504px;
  }
  .title { display: block; }
  .title-the {
    display: flex; align-items: center; gap: 16px;
    font-family: "Arvo", serif; font-weight: 400; font-size: 48px; line-height: 1.2;
    color: var(--rule);
  }
  .title-the::before, .title-the::after {
    content: ""; flex: 1; height: 4px; background: var(--rule);
  }
  .title-quiet {
    display: flex; justify-content: space-between;
    font-family: "Arvo", serif; font-weight: 400; font-size: 96px; line-height: 1;
    color: var(--brown-light); margin-top: 10px;
  }
  .title-ledger {
    display: flex; justify-content: space-between;
    font-family: "Arvo", serif; font-weight: 400; font-size: 100px; line-height: 1;
    color: var(--brown-dark); margin-top: 8px;
  }
  .title-rule { display: block; height: 4px; background: var(--rule); margin-top: 16px; }
  .subtitle {
    margin: 22px -48px 0;
    text-align: center;
    font-family: "EB Garamond", serif; font-size: 33px; line-height: 1.2;
    color: var(--ink-grey);
  }
  .volume {
    position: absolute; top: 1010px; left: 0; right: 0;
    text-align: center;
    font-family: "EB Garamond", serif; font-size: 20px; letter-spacing: 0.42em;
    color: var(--brown-light);
  }
</style>
</head>
<body>
  <main class="cover">
    <p class="author">KB MORROW</p>
    <div class="outlier-art" role="img" aria-label="Illustration: a group of grey game pawns marked with dollar signs, with one taller red pawn standing out in the centre"></div>
    <div class="title-block">
      <h1 class="title">
        <span class="title-the">THE</span>
        <span class="title-quiet"><span>Q</span><span>U</span><span>I</span><span>E</span><span>T</span></span>
        <span class="title-ledger"><span>L</span><span>E</span><span>D</span><span>G</span><span>E</span><span>R</span></span>
        <span class="title-rule"></span>
      </h1>
      <p class="subtitle">Habits for Lasting Security,<br>Calm Savings, and a Full Future</p>
    </div>
    <p class="volume">Volume 1: Foundations</p>
  </main>
</body>
</html>
```